Bookcover: Ways to Turn Into a Bold Pathfinder

I am publishing a super-low-cost innovation book for €4,99 on Quillmere Open Press to help everyone become a great innovator: young ambitious people without college education nor a big budget. Do you want to help me?

Brief:
Design a book cover 1600 x 2560 pixels for QOP.
Main title: Ways to Turn Into a Bold Pathfinder
Sub title: mindset - insights - skills & tools
Author: Joost ter Brakel
Design: captive, and appealing to everyone
Target Group: young ambitious people without college education

For quillmere please format the height/width ratio of 1.6:1

```html
<!DOCTYPE html>
<html lang="en">
<head>
<meta charset="utf-8">
<title>Ways to Turn Into a Bold Pathfinder — Book Cover</title>
<link rel="stylesheet" href="https://fonts.googleapis.com/css2?family=Anton&family=Jost:wght@500&family=Poppins:wght@600;700;800&display=swap">
<style>
  :root {
    --backdrop: #c6c6c6;
    --sky-teal: #0f6f8c;
    --sky-blue: #5b86b0;
    --sky-lavender: #a99bb0;
    --haze-peach: #d9b48e;
    --sun-core: #fff8d8;
    --sun-gold: #f3c35a;
    --city-amber: #c9822e;
    --ground-brown: #3a1406;
    --band-black: #000000;
    --ember: #e8700f;
    --rule-red: #7a1c08;
    --title-ink: #0a0a0a;
    --title-white: #ffffff;
    --title-shade: rgba(38, 10, 22, 0.88);
    --author-gold: #e7b24b;
  }
  * { box-sizing: border-box; margin: 0; padding: 0; }
  html, body {
    width: 808px; height: 1200px; overflow: hidden;
    background: var(--backdrop);
  }
  .cover {
    position: absolute; left: 29px; top: 0;
    width: 750px; height: 1200px; overflow: hidden;
    background: var(--band-black);
  }
  .cover-photo {
    position: absolute; left: 0; top: 0; width: 750px; height: 994px;
    background:
      radial-gradient(circle at 50% 71%, var(--sun-core) 0, rgba(255,240,180,0.9) 90px, rgba(243,195,90,0.55) 190px, rgba(243,195,90,0) 300px),
      linear-gradient(180deg, transparent 0, transparent 88%, rgba(58,20,6,0.85) 93%, var(--ground-brown) 100%),
      linear-gradient(180deg, var(--sky-teal) 0%, var(--sky-blue) 22%, var(--sky-lavender) 40%, var(--haze-peach) 58%, var(--sun-gold) 75%, var(--city-amber) 86%, var(--ground-brown) 100%);
  }
  .title-block {
    position: absolute; left: 0; top: 112px; width: 750px;
    text-align: center;
  }
  .title-lead {
    font-family: "Poppins", sans-serif; font-weight: 700;
    font-size: 34px; letter-spacing: 0.42em; line-height: 1;
    color: var(--title-ink); padding-left: 0.42em;
  }
  .title-accent {
    display: flex; align-items: center; justify-content: center;
    gap: 12px; margin-top: 6px;
  }
  .title-accent .rule {
    width: 132px; height: 5px; background: var(--rule-red);
  }
  .title-accent .word {
    font-family: "Poppins", sans-serif; font-weight: 800;
    font-size: 112px; line-height: 0.95; color: var(--title-white);
    letter-spacing: -0.01em;
  }
  .title-main {
    font-family: "Anton", sans-serif;
    font-size: 168px; line-height: 1; margin-top: 4px;
    letter-spacing: 0;
    color: var(--title-shade);
  }
  .band-rule {
    position: absolute; left: 60px; width: 630px; height: 3px;
    background: linear-gradient(90deg, transparent, var(--ember) 30%, var(--ember) 70%, transparent);
  }
  .band-rule.top { top: 992px; }
  .band-rule.bottom { top: 1072px; }
  .subtitle {
    position: absolute; left: 0; top: 1018px; width: 750px;
    text-align: center;
    font-family: "Jost", sans-serif; font-weight: 500;
    font-size: 27px; letter-spacing: 0.08em; line-height: 1;
    color: var(--title-white); text-transform: uppercase;
  }
  .author {
    position: absolute; left: 0; top: 1101px; width: 750px;
    text-align: center;
    font-family: "Poppins", sans-serif; font-weight: 700;
    font-size: 34px; letter-spacing: 0.2em; line-height: 1;
    color: var(--author-gold); padding-left: 0.2em;
    text-transform: uppercase;
  }
</style>
</head>
<body>
  <main class="cover">
    <div class="cover-photo" role="img" aria-label="Photograph of a man seen from behind with raised fists, standing on a rooftop step against a glowing sunrise over a city skyline, under a blue cloudy sky"></div>

    <h1 class="title-block">
      <span class="title-lead" style="display:block">WAYS TO TURN INTO A</span>
      <span class="title-accent">
        <span class="rule"></span>
        <span class="word">BOLD</span>
        <span class="rule"></span>
      </span>
      <span class="title-main" style="display:block">PATHFINDER</span>
    </h1>

    <div class="band-rule top"></div>
    <p class="subtitle">Mindset - Insights - Skills &amp; Tools</p>
    <div class="band-rule bottom"></div>
    <p class="author">Joost ter Brakel</p>
  </main>
</body>
</html>
```